Simple and Clean business card design

We would like the design to be simple clean and to incorporate our colors.

We are open to your design and talent, we have the dots in our logo as we think of it as data points and we connect data points for people.

We are open to see the great creative and clean design you bring to the table

Contact Information for Business Card

please include: name, position, email, phone and website

Font styles to use
Sans Serif

Requirements
Must have
• my colors incorporated, simplicity
Nice to have
• lots of white space, simplicity
Should not have
• complexicity/ complex art

```html
<!DOCTYPE html>
<html lang="en">
<head>
<meta charset="utf-8">
<title>Vellora — Business Card</title>
<link rel="stylesheet" href="https://fonts.googleapis.com/css2?family=Montserrat:wght@600&family=Arimo:wght@400;700&display=swap">
<style>
  :root {
    --stage: #1f1f1f;
    --ink: #000000;
    --paper: #ffffff;
    --green: #34a853;
    --yellow: #fbbc05;
    --red: #ea4335;
    --blue: #4285f4;
    --icon-blue: #4a7fcf;
  }
  * { box-sizing: border-box; margin: 0; padding: 0; }
  html, body {
    width: 1200px; height: 1015px; overflow: hidden;
    background: var(--stage);
    font-family: "Arimo", Arial, sans-serif;
  }
  .stage {
    position: relative; width: 1200px; height: 1015px;
    display: flex; flex-direction: column; align-items: center; justify-content: center; gap: 50px;
  }
  .card {
    position: relative; width: 540px; height: 310px; overflow: hidden;
    box-shadow: 0 14px 30px rgba(0,0,0,.55);
  }

  /* Wordmark */
  .wordmark {
    display: flex; align-items: center; gap: 10px;
    font-family: "Montserrat", Arial, sans-serif; font-weight: 600;
    font-size: 58px; letter-spacing: 1px; line-height: 1;
  }
  .wordmark-dot { width: 22px; height: 22px; border-radius: 50%; background: var(--blue); flex: none; }

  /* Front */
  .card-front { background: var(--ink); }
  .card-front .wordmark {
    position: absolute; left: 0; right: 0; top: 112px; justify-content: center; color: var(--paper);
  }
  .front-stripes {
    position: absolute; left: 0; right: 0; bottom: 0; height: 20px;
    display: flex; gap: 4px;
  }
  .front-stripes span { flex: 1; }
  .stripe-green { background: var(--green); }
  .stripe-yellow { background: var(--yellow); }
  .stripe-red { background: var(--red); }

  /* Back */
  .card-back { background: var(--paper); }
  .card-back .wordmark {
    position: absolute; left: 0; right: 0; top: 52px; justify-content: center; color: var(--ink);
  }
  .name-band {
    position: absolute; left: 0; right: 0; top: 148px; height: 36px;
    background: var(--ink);
    display: flex; align-items: center; justify-content: center; gap: 14px;
  }
  .person-name { color: var(--paper); font-weight: 700; font-size: 21px; letter-spacing: .5px; }
  .name-divider { color: var(--blue); font-size: 18px; }
  .person-role { color: var(--blue); font-size: 16px; letter-spacing: .5px; }

  .contact-row {
    position: absolute; left: 0; right: 0; bottom: 0; height: 84px;
    display: flex; gap: 5px;
  }
  .contact-item {
    position: relative; flex: 1;
    display: flex; align-items: flex-end; justify-content: center; padding-bottom: 20px;
    color: var(--paper); font-size: 14px; letter-spacing: .3px;
  }
  .contact-phone { background: var(--green); }
  .contact-email { background: var(--yellow); font-size: 13px; }
  .contact-web { background: var(--red); }
  .contact-icon {
    position: absolute; top: -22px; left: 38px;
    width: 44px; height: 44px; border-radius: 50%;
    background: var(--paper); padding: 4px;
  }
  .contact-icon svg { display: block; width: 36px; height: 36px; }
</style>
</head>
<body>
<main class="stage">

  <section class="card card-front" aria-label="Card front">
    <div class="wordmark"><span class="wordmark-dot"></span>vellora</div>
    <div class="front-stripes">
      <span class="stripe-green"></span><span class="stripe-yellow"></span><span class="stripe-red"></span>
    </div>
  </section>

  <section class="card card-back" aria-label="Card back">
    <div class="wordmark"><span class="wordmark-dot"></span>vellora</div>

    <div class="name-band">
      <span class="person-name">DANIEL CROWE</span>
      <span class="name-divider">|</span>
      <span class="person-role">Founder/ CEO</span>
    </div>

    <div class="contact-row">
      <div class="contact-item contact-phone">
        <span class="contact-icon">
          <svg viewBox="0 0 36 36" aria-hidden="true">
            <circle cx="18" cy="18" r="16" fill="none" stroke="var(--icon-blue)" stroke-width="2.5"/>
            <path d="M11 13c0 7 5 12 12 12l2-3-3-2-2 1.5c-2-1-4-3-5-5l1.5-2-2-3z" fill="var(--icon-blue)"/>
            <path d="M19 11a6 6 0 0 1 6 6M19 14a3 3 0 0 1 3 3" fill="none" stroke="var(--icon-blue)" stroke-width="1.6" stroke-linecap="round"/>
          </svg>
        </span>
        555-214-0387
      </div>
      <div class="contact-item contact-email">
        <span class="contact-icon">
          <svg viewBox="0 0 36 36" aria-hidden="true">
            <circle cx="18" cy="18" r="16" fill="none" stroke="var(--icon-blue)" stroke-width="2.5"/>
            <rect x="9" y="12" width="18" height="12" rx="1" fill="var(--icon-blue)"/>
            <path d="M9.5 12.5 18 19l8.5-6.5" fill="none" stroke="#fff" stroke-width="1.5"/>
          </svg>
        </span>
        daniel.crowe@vellora.one
      </div>
      <div class="contact-item contact-web">
        <span class="contact-icon">
          <svg viewBox="0 0 36 36" aria-hidden="true">
            <circle cx="18" cy="18" r="16" fill="none" stroke="var(--icon-blue)" stroke-width="2.5"/>
            <g fill="none" stroke="var(--icon-blue)" stroke-width="1.6">
              <circle cx="18" cy="18" r="9"/>
              <ellipse cx="18" cy="18" rx="4" ry="9"/>
              <path d="M9 18h18M10.5 13.5h15M10.5 22.5h15"/>
            </g>
          </svg>
        </span>
        www.Vellora.one
      </div>
    </div>
  </section>

</main>
</body>
</html>
```